Pitch Deck Powerpoint Template for Entrepreneurship/Education Based Nonprofit

I need a stylish powerpoint design for a start-up nonprofit called Harbor Venture Works (HVW). I am building HVWs pitch deck to raise money. HVW is an entrepreneurial incubator and accelerator that seeks to identify, validate, test, and launch innovative ventures that improve public education. An example of our model, and one of our partners, is Kestrel Schools in New Orleans and New York :http://kestrelsch.example.org

We need the deck to look sleek and innovative - like a start-up pitch deck. Lots of different templates and fonts that pop off the page.

Target Market(s)

Individuals, foundations, and any other stakeholder - we are pitching a new business model and asking for money.

Industry/Entity Type

Building

Font styles to use
Sans Serif

Requirements
Must have
• A sleek/modern feel with several different template slides. charts and graphs/ strong fonts that pop off the page, use of the logo:
• It would be great to have a slide describing the 3 primary programs at Harbor Venture Works (HVW):
• - HVWspark - come in with an idea for an innovation in education, and we will do a two day workshop to examine your business assumptions and discuss next steps.
• - HVWpropell - take your idea to a prototype and launch to customers - we help you with an intensive 30 day program
• - HVWnurture - for existing nonprofit projects, we allow you to work under our umbrella to launch and build capacity
• Slides: Problem Definition, Solution, Value Proposition, Data/MEasurement, Key Partners, About the founder, Key Advisors

```html
<!DOCTYPE html>
<html lang="en">
<head>
<meta charset="utf-8">
<title>Data/Measurement – Harbor Venture Works</title>
<link rel="stylesheet" href="https://fonts.googleapis.com/css2?family=Lato:wght@400;700;900&display=swap">
<style>
  :root {
    --navy: #10336f;
    --panel: #0f3a7a;
    --east: #0c2b5c;
    --west: #0f3c84;
    --north: #a5aabe;
    --accent: #8a1f78;
    --grid: #c8c8c8;
    --ink: #1a1a1a;
    --bg: #ffffff;
  }
  html, body {
    margin: 0;
    padding: 0;
    overflow: hidden;
    background: var(--bg);
  }
  .slide {
    position: relative;
    width: 1200px;
    height: 675px;
    overflow: hidden;
    background: var(--bg);
    font-family: "Lato", Arial, sans-serif;
  }
  .slide-title {
    position: absolute;
    left: 92px;
    top: 58px;
    margin: 0;
    font-size: 64px;
    font-weight: 700;
    color: var(--navy);
    letter-spacing: -0.5px;
    line-height: 1;
  }
  .brand {
    position: absolute;
    left: 880px;
    top: 28px;
    display: flex;
    align-items: center;
    gap: 14px;
  }
  .brand-dot {
    width: 22px;
    height: 22px;
    border-radius: 50%;
    background: var(--navy);
  }
  .brand-name {
    font-size: 32px;
    font-weight: 900;
    color: var(--navy);
    line-height: 1.0;
  }
  .rule-main {
    position: absolute;
    left: 75px;
    top: 148px;
    width: 1125px;
    height: 20px;
    background: var(--navy);
  }
  .rule-accent {
    position: absolute;
    left: 0;
    top: 153px;
    width: 67px;
    height: 10px;
    background: var(--accent);
  }
  .description {
    position: absolute;
    left: 80px;
    top: 187px;
    width: 212px;
    height: 408px;
    box-sizing: border-box;
    padding: 28px 22px;
    background: var(--panel);
    color: #fff;
    font-size: 21px;
    line-height: 1.4;
  }
  .description p { margin: 0; }
  .chart {
    position: absolute;
    left: 317px;
    top: 200px;
    width: 850px;
    height: 400px;
  }
  .chart text { font-family: "Lato", Arial, sans-serif; fill: var(--ink); }
  .chart .chart-title { font-size: 15px; font-weight: 700; }
  .chart .axis-label { font-size: 13px; }
  .chart .grid { stroke: var(--grid); stroke-width: 0.8; }
  .bar-east { fill: var(--east); }
  .bar-west { fill: var(--west); }
  .bar-north { fill: var(--north); }
</style>
</head>
<body>
<main class="slide">
  <h1 class="slide-title">Data/Measurement</h1>

  <div class="brand">
    <span class="brand-dot"></span>
    <span class="brand-name">Harbor<br>Venture Works</span>
  </div>

  <div class="rule-main"></div>
  <div class="rule-accent"></div>

  <aside class="description">
    <p>Description area.</p>
  </aside>

  <svg class="chart" viewBox="190 120 510 240" role="img" aria-label="Bar chart of quarterly values for East, West and North">
    <text class="chart-title" x="437" y="143" text-anchor="middle">Title</text>

    <g class="grid-lines">
      <line class="grid" x1="240" y1="166" x2="680" y2="166"/>
      <line class="grid" x1="240" y1="191" x2="680" y2="191"/>
      <line class="grid" x1="240" y1="216" x2="680" y2="216"/>
      <line class="grid" x1="240" y1="241" x2="680" y2="241"/>
      <line class="grid" x1="240" y1="266" x2="680" y2="266"/>
      <line class="grid" x1="240" y1="291" x2="680" y2="291"/>
    </g>

    <g class="y-axis axis-label" text-anchor="end">
      <text class="axis-label" x="235" y="171">100</text>
      <text class="axis-label" x="235" y="196">80</text>
      <text class="axis-label" x="235" y="221">60</text>
      <text class="axis-label" x="235" y="246">40</text>
      <text class="axis-label" x="235" y="271">20</text>
      <text class="axis-label" x="235" y="296">0</text>
    </g>

    <g class="series-east">
      <rect class="bar-east" x="249" y="266" width="29" height="25"/>
      <rect class="bar-east" x="359" y="256.5" width="29" height="34.5"/>
      <rect class="bar-east" x="469" y="178.5" width="29" height="112.5"/>
      <rect class="bar-east" x="579" y="266" width="29" height="25"/>
    </g>
    <g class="series-west">
      <rect class="bar-west" x="278" y="253" width="29" height="38"/>
      <rect class="bar-west" x="388" y="242" width="29" height="49"/>
      <rect class="bar-west" x="498" y="247" width="29" height="44"/>
      <rect class="bar-west" x="608" y="252" width="29" height="39"/>
    </g>
    <g class="series-north">
      <rect class="bar-north" x="307" y="233" width="30" height="58"/>
      <rect class="bar-north" x="417" y="232" width="30" height="59"/>
      <rect class="bar-north" x="527" y="234.5" width="30" height="56.5"/>
      <rect class="bar-north" x="637" y="236" width="30" height="55"/>
    </g>

    <g class="x-axis" text-anchor="middle">
      <text class="axis-label" x="295" y="318">1st Qtr</text>
      <text class="axis-label" x="405" y="318">2nd Qtr</text>
      <text class="axis-label" x="515" y="318">3rd Qtr</text>
      <text class="axis-label" x="625" y="318">4th Qtr</text>
    </g>

    <g class="legend">
      <rect class="bar-east" x="355" y="341" width="9" height="9"/>
      <text class="axis-label" x="368" y="350">East</text>
      <rect class="bar-west" x="410" y="341" width="9" height="9"/>
      <text class="axis-label" x="423" y="350">West</text>
      <rect class="bar-north" x="474" y="341" width="9" height="9"/>
      <text class="axis-label" x="487" y="350">North</text>
    </g>
  </svg>
</main>
</body>
</html>
```